Harcourt Power Gym Chronic Pain Flyer

Double sided DL flyer required to promote a strength training studio to sufferers of chronic pain. Flyer will be displayed in osteopathy, chiropractic and massage clinics. Flyer should be clean, professional and appeal to an older (40+) demographic.

Target Market(s)

Chronic pain sufferers. Age 40+

Industry/Entity Type

Health And Wellness

Colors

Designer to choose colors to be used in the design.

Requirements
Must have
• See attached files for text copy and logo. Image(s) of people strength training with a coach or personal trainer, as well as images depicting pain in common parts of the body (such as those pictured in the supplied mock up)
• website address: harcourtpowergym.com.au
• phone number : 0458 214 963
• Street address: 3/14 Birchwood Rd, Harcourt
Nice to have
• Images such as in the attached files.

```html
<!DOCTYPE html>
<html lang="en">
<head>
<meta charset="utf-8">
<title>Harcourt Power Gym – DL Flyer</title>
<link href="https://fonts.googleapis.com/css2?family=Lato:wght@400;700;900&display=swap" rel="stylesheet">
<style>
  :root{
    --stage:#3a3a3a;
    --red:#cc1f26;
    --white:#ffffff;
    --ink:#1f1f1f;
    --charcoal:#3d3d3d;
    --label:#e6e6e6;
  }
  *{margin:0;padding:0;box-sizing:border-box}
  html,body{width:1200px;height:1200px;overflow:hidden;background:var(--stage);font-family:'Lato',sans-serif}
  .stage{position:relative;width:1200px;height:1200px}
  .flyer{position:absolute;width:446px;height:918px;background:var(--white);overflow:hidden;box-shadow:0 4px 14px rgba(0,0,0,.45)}
  .flyer--front{left:116px;top:128px}
  .flyer--back{left:622px;top:126px}
  .flyer__shapes{position:absolute;inset:0;width:446px;height:918px}
  .brand{position:absolute;left:0;right:0;text-align:center;color:var(--charcoal);font-weight:900;line-height:1}
  .brand__main{display:block;font-size:40px;letter-spacing:2px}
  .brand__sub{display:block;font-size:20px;letter-spacing:5px;margin-top:6px}
  .flyer--front .brand{top:62px}
  .flyer--back .brand{top:52px}
  .headline{position:absolute;left:0;right:0;text-align:center;color:var(--white);line-height:1}
  .headline__lead{position:absolute;top:630px;left:0;right:0;font-size:44px;font-weight:700;letter-spacing:-.3px}
  .headline__main{position:absolute;top:694px;left:0;right:0;font-size:77px;font-weight:900;letter-spacing:-1px}
  .contact{position:absolute;left:0;right:0}
  .contact__phone{display:flex;align-items:center;font-weight:900;font-size:37px;line-height:1}
  .contact__phone svg{width:36px;height:36px;margin-right:8px}
  .contact__line{display:flex;align-items:center;font-size:17px;margin-top:8px;line-height:1.2}
  .contact__line svg{width:18px;height:18px;margin-right:10px}
  .flyer--front .contact{top:808px;left:66px}
  .flyer--front .contact__phone{color:var(--red)}
  .flyer--front .contact__line{color:var(--ink)}
  .flyer--front .contact__line:first-of-type{margin-top:10px}
  .flyer--back .contact{top:780px;left:68px;color:var(--white)}
  .tagline{position:absolute;top:160px;left:0;right:0;height:48px;background:var(--red);color:var(--white);font-size:30px;font-weight:700;display:flex;align-items:center;justify-content:center}
  .copy{position:absolute;left:26px;right:22px;color:var(--ink);font-size:17.5px;line-height:21.6px;text-align:justify}
  .copy--intro{top:219px;text-align:left}
  .copy--detail{top:448px}
  .copy strong{font-weight:700}
  .label{position:absolute;top:1076px;color:var(--label);font-size:38px;font-weight:400;width:200px;text-align:center}
  .label--front{left:227px}
  .label--back{left:745px}
</style>
</head>
<body>
<main class="stage">

  <section class="flyer flyer--front" aria-label="Flyer front">
    <svg class="flyer__shapes" viewBox="0 0 446 918">
      <defs>
        <linearGradient id="frontPhotoBase" x1="0" y1="0" x2="0" y2="1">
          <stop offset="0" stop-color="#b9aca2"/>
          <stop offset=".3" stop-color="#6e5c52"/>
          <stop offset=".7" stop-color="#5a4a42"/>
          <stop offset="1" stop-color="#3e332e"/>
        </linearGradient>
        <radialGradient id="frontPhotoLight" cx=".55" cy=".55" r=".55">
          <stop offset="0" stop-color="#a5948a" stop-opacity=".8"/>
          <stop offset="1" stop-color="#a5948a" stop-opacity="0"/>
        </radialGradient>
        <linearGradient id="frontPhotoTop" x1="0" y1="0" x2="0" y2="1">
          <stop offset="0" stop-color="#d8cdc4"/>
          <stop offset="1" stop-color="#d8cdc4" stop-opacity="0"/>
        </linearGradient>
      </defs>
      <g role="img" aria-label="Photo: practitioner's hand on a client's bare back">
        <rect x="0" y="150" width="446" height="500" fill="url(#frontPhotoBase)"/>
        <rect x="0" y="150" width="446" height="500" fill="url(#frontPhotoLight)"/>
        <rect x="0" y="150" width="446" height="150" fill="url(#frontPhotoTop)"/>
      </g>
      <path d="M0 0H446V172Q240 205 0 166Z" fill="var(--white)"/>
      <path d="M0 166Q240 205 446 172" fill="none" stroke="#a8a8a8" stroke-width="4"/>
      <path d="M0 526Q230 650 446 530V640H0Z" fill="#8f8f8f"/>
      <path d="M0 556Q230 640 446 548V802H0Z" fill="var(--red)"/>
      <rect x="0" y="802" width="446" height="104" fill="var(--white)"/>
      <rect x="0" y="906" width="446" height="12" fill="var(--red)"/>
    </svg>
    <div class="brand"><span class="brand__main">HARCOURT</span><span class="brand__sub">POWER GYM</span></div>
    <div class="headline">
      <span class="headline__lead">HEALTH THROUGH</span>
      <span class="headline__main">STRENGTH</span>
    </div>
    <div class="contact">
      <div class="contact__phone">
        <svg viewBox="0 0 36 36"><circle cx="18" cy="18" r="16.5" fill="none" stroke="#8a8a8a" stroke-width="2"/><path d="M12 10c1-1 2-1 3 0l2 3c.6 1 .3 1.7-.4 2.3l-1 .8c.8 2 2.4 3.8 4.6 4.8l.9-1c.6-.7 1.4-.9 2.3-.3l3 2c1 .8.9 1.8 0 2.7-2 2-4.5 2.2-8 .2-3.6-2.2-6-5.4-7.2-9-.6-2.2-.3-4.5.8-5.5z" fill="#8a8a8a"/></svg>
        0458 214 963
      </div>
      <div class="contact__line">
        <svg viewBox="0 0 18 18"><circle cx="9" cy="9" r="7.5" fill="none" stroke="#8a8a8a" stroke-width="1.4"/><ellipse cx="9" cy="9" rx="3.2" ry="7.5" fill="none" stroke="#8a8a8a" stroke-width="1.2"/><path d="M1.5 9h15M3 5h12M3 13h12" stroke="#8a8a8a" stroke-width="1.1"/></svg>
        harcourtpowergym.com.au
      </div>
      <div class="contact__line">
        <svg viewBox="0 0 18 18"><path d="M9 1.5a5.5 5.5 0 0 0-5.5 5.5c0 4 5.5 9.5 5.5 9.5s5.5-5.5 5.5-9.5A5.5 5.5 0 0 0 9 1.5z" fill="#8a8a8a"/><circle cx="9" cy="7" r="2" fill="var(--white)"/></svg>
        3/14 Birchwood Rd, Harcourt
      </div>
    </div>
  </section>

  <section class="flyer flyer--back" aria-label="Flyer back">
    <svg class="flyer__shapes" viewBox="0 0 446 918">
      <defs>
        <linearGradient id="backPhoto" x1="0" y1="0" x2="0" y2="1">
          <stop offset="0" stop-color="#ffffff"/>
          <stop offset=".2" stop-color="#e4ddd8"/>
          <stop offset=".6" stop-color="#b8ada6"/>
          <stop offset="1" stop-color="#8a7e77"/>
        </linearGradient>
        <radialGradient id="backPhotoLight" cx=".45" cy=".6" r=".5">
          <stop offset="0" stop-color="#efe8e3" stop-opacity=".7"/>
          <stop offset="1" stop-color="#efe8e3" stop-opacity="0"/>
        </radialGradient>
        <radialGradient id="painLowerBack" cx=".5" cy=".72" r=".7">
          <stop offset="0" stop-color="#e2414c"/>
          <stop offset=".25" stop-color="#dc9a9c"/>
          <stop offset=".55" stop-color="#c9c6c5"/>
          <stop offset="1" stop-color="#9a9796"/>
        </radialGradient>
        <radialGradient id="painShoulder" cx=".52" cy=".42" r=".7">
          <stop offset="0" stop-color="#e2414c"/>
          <stop offset=".25" stop-color="#d9a3a3"/>
          <stop offset=".55" stop-color="#bdbab9"/>
          <stop offset="1" stop-color="#858281"/>
        </radialGradient>
        <radialGradient id="painKnee" cx=".48" cy=".5" r=".7">
          <stop offset="0" stop-color="#e2414c"/>
          <stop offset=".28" stop-color="#d68e92"/>
          <stop offset=".55" stop-color="#a9a5a4"/>
          <stop offset="1" stop-color="#6f6b6a"/>
        </radialGradient>
      </defs>
      <g role="img" aria-label="Photo: coach working on a client's shoulder">
        <rect x="0" y="500" width="446" height="260" fill="url(#backPhoto)"/>
        <rect x="0" y="500" width="446" height="260" fill="url(#backPhotoLight)"/>
      </g>
      <path d="M0 688Q223 790 446 676V712Q223 800 0 724Z" fill="var(--white)"/>
      <path d="M0 722Q223 800 446 710V918H0Z" fill="var(--red)"/>
      <g stroke="var(--red)" stroke-width="2.5">
        <circle role="img" aria-label="Image: lower back pain" cx="77" cy="359" r="62" fill="url(#painLowerBack)"/>
        <circle role="img" aria-label="Image: shoulder pain" cx="219" cy="359" r="62" fill="url(#painShoulder)"/>
        <circle role="img" aria-label="Image: knee pain" cx="361" cy="359" r="62" fill="url(#painKnee)"/>
      </g>
    </svg>
    <div class="brand"><span class="brand__main">HARCOURT</span><span class="brand__sub">POWER GYM</span></div>
    <div class="tagline">You Don’t have to live in pain.</div>
    <p class="copy copy--intro"><strong>Strength</strong> training has been shown to improve many chronic pain conditions and is now being routinely recommended by medical and health professionals.</p>
    <p class="copy copy--detail">Our private studio provides high quality strength training by expert strength coaches. We’ve helped countless people improve or eliminate chronic pain, contact us today and find out how we can help you.</p>
    <div class="contact">
      <div class="contact__phone">
        <svg viewBox="0 0 36 36"><circle cx="18" cy="18" r="16.5" fill="none" stroke="#fff" stroke-width="2"/><path d="M12 10c1-1 2-1 3 0l2 3c.6 1 .3 1.7-.4 2.3l-1 .8c.8 2 2.4 3.8 4.6 4.8l.9-1c.6-.7 1.4-.9 2.3-.3l3 2c1 .8.9 1.8 0 2.7-2 2-4.5 2.2-8 .2-3.6-2.2-6-5.4-7.2-9-.6-2.2-.3-4.5.8-5.5z" fill="#fff"/></svg>
        0458 214 963
      </div>
      <div class="contact__line">
        <svg viewBox="0 0 18 18"><circle cx="9" cy="9" r="7.5" fill="none" stroke="#fff" stroke-width="1.4"/><ellipse cx="9" cy="9" rx="3.2" ry="7.5" fill="none" stroke="#fff" stroke-width="1.2"/><path d="M1.5 9h15M3 5h12M3 13h12" stroke="#fff" stroke-width="1.1"/></svg>
        harcourtpowergym.com.au
      </div>
      <div class="contact__line">
        <svg viewBox="0 0 18 18"><path d="M9 1.5a5.5 5.5 0 0 0-5.5 5.5c0 4 5.5 9.5 5.5 9.5s5.5-5.5 5.5-9.5A5.5 5.5 0 0 0 9 1.5z" fill="#fff"/><circle cx="9" cy="7" r="2" fill="var(--red)"/></svg>
        3/14 Birchwood Rd, Harcourt
      </div>
    </div>
  </section>

  <p class="label label--front">Front</p>
  <p class="label label--back">Back</p>
</main>
</body>
</html>
```